Flowy subpage design wanted for a modern tax/accounting firm in Switzerland

--- Introduction ---
We are a tax and accounting firm in Switzerland. We provide services for expats living in Switzerland, our service is quite exclusive and modern (digital).

We just relaunched our website www.fiscavantra.ch and are happy with the design, so the desired subpage (more details below) should of course fit in.

--- Main brief ---
Please see Word File attached. The page has to include the whole text (11 chapters). A very intuitive, flowy design on only one subpage (not one page per chapter) is a MUST. Also, it is key that the design is supporting the content of the individual chapters, so it would be advantageous if you'd have a good unterstanding of the text attached.

--- Further information ---
A similar example would be this one: https://www2.brennick.com/ch/en/pages/tax/articles/living-working-switzerland.html

This one is similar in what concerns the content, but NOT what we are looking for designwise. It is very simple and looks "thrown together", just not aesthetically pleasing in our opinion.

--- Final thoughts ---
- If you blow our minds with your design, we will certainly have future work for you.
- Our clients are between 20-50 years old, well educated, high income / high wealth, English speaking and living in Switzerland.
- CI/CD information:
Fonts
Montserrat regular / medium italic / bold
Colors
White #ffffffff
Darkblue #0a2b46
Darkblue 25% #b5bfc8
Darkblue 50% #8595a4
Greenblue #0d4261

We are looking forward to your designs!
Updates

Thank you very much for the submitted designs and your efforts. Unfortunately, none of the designs meet our expectations so far. Please note the following: - Designs that do not take CI into account will not be looked at more closely. - We have received many simple designs with very simple structure and accordion elements. But more important than the simple structure is an eye-catching design! Make it flowy and beautiful - We don't want pictures of Swiss vehicles, passes or other pictures that don't actively support the text. If you can make an illustration that really fits the context, fine, otherwise better leave it without. Thank you

Target Market(s)

Expats living in Switzerland. High income earners / high net worth individuals

Industry/Entity Type

tax/accounting

Number of Pages Required

1 page

Font styles to use
Other font styles liked:
• Montserrat

Colors
0054AA
0677BA
7BADD7
CADEEF
E8F1F8

Requirements
Must have
• based on general website design
Nice to have
• intuitive, flowy, attractive representation of much text
Should not have
• basic copy/paste of the text in sections :)

```html
<!DOCTYPE html>
<html lang="en">
<head>
<meta charset="utf-8">
<title>Switzerland – Swiss tax guide | Fiscavantra Advisory</title>
<link href="https://fonts.googleapis.com/css2?family=Montserrat:ital,wght@0,400;0,500;0,600;0,700;1,500&display=swap" rel="stylesheet">
<style>
  :root{
    --white:#ffffff;
    --darkblue:#0a2b46;
    --darkblue-25:#b5bfc8;
    --darkblue-50:#8595a4;
    --greenblue:#0d4261;
    --blue-strong:#0054aa;
    --blue-mid:#0677ba;
    --blue-light:#7badd7;
    --blue-pale:#cadeef;
    --blue-mist:#e8f1f8;
    --ink:#1d2a36;
    --grey-tile:#8e9396;
    --slate-tile:#4d545b;
    --night-tile:#0b0f1c;
  }
  *{box-sizing:border-box;margin:0;padding:0}
  html,body{width:1200px;height:3622px;overflow:hidden;background:var(--white)}
  body{font-family:'Montserrat',sans-serif;color:var(--ink);position:relative}

  /* Header */
  .site-header{position:absolute;top:0;left:0;width:1200px;height:56px;background:#f3f4f5;border-bottom:1px solid #e1e3e5;z-index:5}
  .brand{position:absolute;left:101px;top:9px;display:flex;align-items:center;gap:8px;height:38px}
  .brand-dot{width:34px;height:34px;border-radius:50%;border:3px solid var(--darkblue)}
  .brand-name{font-weight:600;font-size:17px;color:var(--darkblue);letter-spacing:.5px;line-height:1}
  .main-nav{position:absolute;left:579px;top:0;height:56px;display:flex;align-items:center}
  .main-nav a{font-size:10px;color:#5f6972;text-decoration:none;height:56px;display:flex;align-items:center;margin-right:20px;white-space:nowrap}
  .main-nav a.active{color:var(--darkblue);font-weight:600;border-bottom:2px solid var(--darkblue);padding:0 10px}
  .caret{font-size:7px;margin-left:3px}
  .calc-btn{position:absolute;left:1006px;top:15px;width:90px;height:28px;background:var(--darkblue);color:var(--white);font-size:10px;display:flex;align-items:center;gap:12px;padding-left:10px}
  .calc-btn svg{flex:none}

  /* Hero */
  .hero{position:absolute;top:56px;left:0;width:1200px;height:300px;overflow:hidden}
  .hero-photo{position:absolute;inset:0;background:
      linear-gradient(180deg,#7fa6cf 0%,#a9c3dd 28%,#c9d6e1 40%,#6f8a73 62%,#3f5f45 100%)}
  .hero-wave{position:absolute;left:0;top:0}
  .hero-title{position:absolute;top:50px;width:100%;text-align:center;font-size:40px;font-weight:500;color:var(--white);letter-spacing:.5px}

  /* Topic grid */
  .topic-grid{position:absolute;top:192px;left:206px;width:787px;display:grid;
    grid-template-columns:repeat(4,196.75px);grid-template-rows:repeat(4,134.25px);z-index:3}
  .tile{position:relative;display:flex;align-items:flex-end;padding:0 18px 22px;color:var(--white);
    font-weight:700;font-size:15.5px;line-height:20px;overflow:hidden}
  .tile span{position:relative;z-index:1}
  .tile .tile-photo{position:absolute;inset:0}
  .t-life{grid-column:1;grid-row:1;background:var(--grey-tile)}
  .t-overview{grid-column:2;grid-row:1/3;background:var(--blue-light)}
  .t-immigrating{grid-column:3/5;grid-row:1;background:var(--night-tile);align-items:center;padding:28px 26px 0}
  .t-indirect{grid-column:1;grid-row:2}
  .t-indirect .tile-photo{background:linear-gradient(160deg,#5f7488,#c7d2dc 45%,#34495d)}
  .t-federal{grid-column:3;grid-row:2}
  .t-federal .tile-photo{background:linear-gradient(180deg,#7d9ec3,#a5b6c6 45%,#4a5860)}
  .t-rent{grid-column:4;grid-row:2;background:var(--blue-mid)}
  .t-dta{grid-column:1/3;grid-row:3;background:var(--greenblue);align-items:center;padding:0 22px}
  .t-childcare{grid-column:3;grid-row:3;background:var(--darkblue);align-items:center;padding:0 18px}
  .t-labor{grid-column:4;grid-row:3/5;background:var(--blue-strong)}
  .t-transport{grid-column:1;grid-row:4;background:var(--slate-tile);padding-left:22px}
  .t-recreation{grid-column:2/4;grid-row:4;padding-left:20px}
  .t-recreation .tile-photo{background:linear-gradient(160deg,#4f6f55,#2f8a9c 50%,#1e5f74)}

  /* Chapter */
  .chapter-banner{position:absolute;top:780px;left:260px;width:593px;height:197px;background:var(--greenblue)}
  .chapter-banner h1{position:absolute;left:41px;top:38px;color:var(--white);font-size:25px;font-weight:700;line-height:31px}
  .chapter-photo{position:absolute;top:800px;left:652px;width:288px;height:157px;
    background:linear-gradient(180deg,#6f7ea3 0%,#c7a98d 40%,#6d6a66 70%,#3a4450 100%)}

  .chapter-body{position:absolute;top:996px;left:260px;width:676px;font-size:10.7px;line-height:18.8px;color:#2a3540}
  .chapter-body p{margin:0}
  .chapter-body h2{font-size:14px;font-weight:700;color:var(--darkblue);line-height:20px;margin:20px 0 17px}
  .chapter-body h3{font-size:12.6px;font-weight:500;color:var(--blue-mid);line-height:20px;margin:20px 0 17px}
  .chapter-body ul{list-style:none;padding-left:40px}
  .chapter-body ul li::before{content:"• "}
  .school-list{list-style:none;padding-left:30px!important;margin:18px 0 20px}
  .school-list li{display:flex;align-items:flex-start;gap:24px;min-height:40px}
  .school-list li::before{content:none!important}
  .school-icon{flex:none;width:25px;height:25px;border-radius:50%;background:var(--blue-mid);display:flex;align-items:center;justify-content:center;margin-top:-3px}
</style>
</head>
<body>

<header class="site-header">
  <div class="brand"><span class="brand-dot"></span><span class="brand-name">FISCAVANTRA<br>ADVISORY</span></div>
  <nav class="main-nav">
    <a href="#">Home</a>
    <a href="#">Tax returns</a>
    <a href="#">More services<span class="caret">▼</span></a>
    <a href="#" class="active">Swiss tax guide</a>
    <a href="#">About us</a>
  </nav>
  <div class="calc-btn">
    <svg width="10" height="13" viewBox="0 0 10 13"><rect x=".5" y=".5" width="9" height="12" fill="none" stroke="#fff"/><rect x="2" y="2" width="6" height="2.5" fill="#fff"/><rect x="2" y="6" width="2" height="1.5" fill="#fff"/><rect x="6" y="6" width="2" height="1.5" fill="#fff"/><rect x="2" y="9" width="2" height="1.5" fill="#fff"/><rect x="6" y="9" width="2" height="1.5" fill="#fff"/></svg>
    Calculate
  </div>
</header>

<section class="hero">
  <div class="hero-photo" role="img" aria-label="Alpine mountain valley under a blue sky with clouds"></div>
  <svg class="hero-wave" width="1200" height="300" viewBox="0 0 1200 300">
    <path d="M993 212 L1200 262 L1200 184 Z" fill="var(--darkblue)"/>
    <path d="M0 288 Q420 270 700 252 Q900 242 1200 280 L1200 300 L0 300 Z" fill="var(--white)"/>
  </svg>
  <div class="hero-title">Switzerland</div>
</section>

<nav class="topic-grid">
  <a class="tile t-life"><span>Life in<br>Switzerland</span></a>
  <a class="tile t-overview"><span>Switzerland - a<br>brief overview of<br>the Alpine<br>country</span></a>
  <a class="tile t-immigrating"><span>Immigrating to Switzerland -<br>These options are available</span></a>
  <a class="tile t-indirect"><div class="tile-photo" role="img" aria-label="Snow-covered mountain peaks"></div><span>Indirect taxes in<br>Switzerland</span></a>
  <a class="tile t-federal"><div class="tile-photo" role="img" aria-label="City riverside with church towers"></div><span>Other federal<br>taxes in<br>Switzerland</span></a>
  <a class="tile t-rent"><span>Rent and buy<br>in Switzerland</span></a>
  <a class="tile t-dta"><span>Double taxation agreements<br>between Switzerland and other<br>countries</span></a>
  <a class="tile t-childcare"><span>Childcare in<br>Switzerland</span></a>
  <a class="tile t-labor"><span>Labor Law in<br>Switzerland - An<br>Overview</span></a>
  <a class="tile t-transport"><span>Public<br>transportation</span></a>
  <a class="tile t-recreation"><div class="tile-photo" role="img" aria-label="Turquoise mountain lake surrounded by forest"></div><span>Recreation</span></a>
</nav>

<div class="chapter-banner"><h1>01<br>Life<br>in Switzerland</h1></div>
<div class="chapter-photo" role="img" aria-label="Old town bridge and church tower at dusk"></div>

<article class="chapter-body">
  <p>To give you a small impression of what to expect when living in Switzerland, we have put together some topics for you to make your new start in Switzerland as pleasant as possible.</p>

  <h2>General</h2>
  <h3>4 official languages</h3>
  <p>Unlike many other countries in Europe, where there is usually only one official national language, Switzerland has four of them:<br>German, French, Italian and Romansh.<br>The most widespread language is German, which is spoken mainly in central Switzerland and the cantons bordering Germany.<br>French dominates in the western part of Switzerland, and Italian in the southeastern part.<br>Rhaeto-Romanic is spoken by only a very small part of the total population in eastern Switzerland.<br>In each region, there are also different dialects in the various languages.<br>Official documents are generally issued in German, French and Italian.</p>

  <h3>Currency and banking</h3>
  <p>The national currency in Switzerland is the Swiss franc (CHF). 1 Swiss franc (Franken) is equal to 100 centimes (Rappen).<br>The banknotes are available in the following amounts: 10, 20, 50, 100, 200, 1000.<br>For coins, there are the following denominations:</p>
  <ul><li>CHF 1, 2, 5</li><li>5, 10, 20, 50 centimes</li></ul>
  <p>Current accounts can be opened at any major bank, Swiss Courier Bank, cantonal or private banks. The largest banks in Switzerland are: Alpenbank Helvetia, Unibank Zurich and Courierbank.</p>

  <h3>Public holidays</h3>
  <p>Public holidays apply throughout Switzerland. In addition, there are cantonal holidays, which may vary from canton to canton.<br>The federal public holidays are:</p>
  <ul>
    <li>January 1: New Year's Day</li>
    <li>Good Friday (variable date)</li>
    <li>Easter Monday (variable date)</li>
    <li>Ascension Day (variable date, 38 days after Easter Monday)</li>
    <li>August 1: Swiss National Day</li>
    <li>December 25: Christmas Day</li>
    <li>December 26: Boxing Day</li>
  </ul>

  <h3>Usual business and store opening hours</h3>
  <p>Government offices and banks are typically open from 8 a.m. to 5 p.m. on weekdays (Monday through Friday), although there may be differences depending on the office.<br>Stores are usually open from 9 a.m. to 6:30 p.m. on weekdays, and from 9 a.m. to 5 p.m. on Saturdays. In cities, stores are often open even later, until 9 pm.<br>Stores, banks and government offices are generally closed on Sundays. Exceptions are stores in train stations, airports or tourist places.</p>

  <h3>Electricity and water</h3>
  <p>The provision and maintenance of the public electricity and water network is the responsibility of the cantons. As a rule, anyone moving into a house or apartment must register their electricity connection with a supplier of their choice. The monthly, quarterly or semi-annual contributions are then paid by means of a progress bill. The energy supplier, as well as the water company, usually prepare a statement at the end of the year, and refund overpaid contributions, or demand an</p>

  <h3>Telephone and television</h3>
  <p>The Swiss telephone network is operated by Helvecom. Anyone who wants to have a telephone or Internet connection must contact Helvecom so that it provides a connection (if not already available). Any service can then be selected as the Internet provider.<br>Every household must pay a broadcasting fee - even if there is no TV or radio. The fees are collected by the RADIVA company.</p>

  <h2>Living in Switzerland</h2>
  <p>The Swiss housing and real estate market varies greatly from region to region in terms of purchase and rental prices. In highly sought-after areas or larger cities, prices are relatively high, while living in rural areas is less expensive.</p>

  <h3>Rent</h3>
  <p>Vacancies are the exception rather than the rule in highly sought-after regions. Often, rental properties are not even published on the Internet, so it is more difficult to find a suitable apartment without a real estate agent. A real estate agent has access to properties before they are published by advertisement. This increases the chances of finding a property for rent.<br>However, the landlord always has the final say. The landlord is not obliged to accept the first applicant.</p>

  <h3>Buy</h3>
  <p>Under certain conditions, it is also possible for non-Swiss nationals to purchase residential property in Switzerland.<br>A down payment of 20% of the purchase price must be made from equity, as a maximum mortgage of 80% of the purchase price can be taken out.<br>The purchase of a property changes the tax situation of the buyer, as the residential property is henceforth included in the assets and is therefore subject to wealth tax (which varies from canton to canton). It is advisable to consult with a tax expert</p>

  <h2>The education system in Switzerland</h2>
  <p>In Switzerland, there are both public and private schools. The public schools are financed by the cantons and attendance at such a school is free of charge.<br>Compulsory kindergarten or schooling begins at the age of 4. A minimum of 11 years of schooling is compulsory.<br>Public educational institutions are classified as follows:</p>
  <ul class="school-list">
    <li><span class="school-icon"><svg width="13" height="13" viewBox="0 0 13 13"><circle cx="6.5" cy="4" r="2.5" fill="#fff"/><rect x="2.5" y="7.5" width="8" height="4" rx="2" fill="#fff"/></svg></span><span>Kindergarten: age 4-6 years; compulsory in most cantons</span></li>
    <li><span class="school-icon"><svg width="13" height="13" viewBox="0 0 13 13"><path d="M1 6 L6.5 2 L12 6 V11 H1 Z" fill="#fff"/></svg></span><span>Elementary school: ages 6-12, grades 1-6, mandatory.</span></li>
    <li><span class="school-icon"><svg width="13" height="13" viewBox="0 0 13 13"><rect x="2" y="1.5" width="9" height="10" fill="none" stroke="#fff" stroke-width="1.4"/><path d="M4 5h5M4 8h5" stroke="#fff" stroke-width="1.2"/></svg></span><span>secondary school: age 12-15, compulsory, leads to completion of compulsory education plan</span></li>
    <li><span class="school-icon"><svg width="13" height="13" viewBox="0 0 13 13"><path d="M1 5 L6.5 2 L12 5 Z" fill="#fff"/><path d="M3 6v4M6.5 6v4M10 6v4" stroke="#fff" stroke-width="1.4"/><rect x="1" y="10.5" width="11" height="1.5" fill="#fff"/></svg></span><span>after secondary school: special schools for preparation for higher education (e.g. university), or training centers for trainees</span></li>
  </ul>
  <p>Anyone wishing to enroll their child in the Swiss public school system must contact the cantonal education authority and provide the following proof:</p>
  <ul><li>Work/residence permit for Switzerland</li><li>Health and accident insurance for the child</li></ul>
  <p>If a foreign child is between the ages of 12 and 15, he or she must pass an entrance exam before enrolling in a public school, which tests, among other things, sufficient proficiency in the language of instruction.<br>Enrolling the child in a private school is also possible. However, depending on the school, waiting times for a free place can be several years.</p>

  <h2>The healthcare system in Switzerland</h2>
  <p>The healthcare system in Switzerland is one of the best in the world. Even in less densely populated regions, the density of hospitals and doctors' offices is high, so that medical care is always timely manner.<br>The federal government sets the financial framework within which health insurers may offer their premiums. The federal government must also give its prior consent to premium increases and can also reject them.<br>The cantons and municipalities are responsible for regulating hospitals. This means that it is determined at the cantonal level which hospital provides which services and how high the wages of doctors and nursing staff are.<br>Compulsory health insurance applies in Switzerland. This means that everyone who lives here must have health insurance.<br>The health insurance companies are private companies, but they are only allowed to operate within the legal framework set by the federal government.<br>The companies are obliged to include every citizen in the so-called basic insurance- without a prior health check<br>Insured persons can add additional services that go beyond basic medical care to their health insurance plan at an additional cost, if they wish.<br>Every citizen is free to choose an insurer. The amount of the insurance premiums that are paid monthly differ in part very much from insurer to insurer. Therefore, it is advisable to compare the benefits and premiums of the individual insurers beforehand.</p>

  <h2>Driving in Switzerland</h2>
  <h3>General information about driving in Switzerland</h3>
  <p>Right-hand traffic applies in Switzerland. Driving a vehicle is permitted for persons 18 years of age and older; trucks and other large vehicles may only be driven from 21 years of age. Fun fact: A small motorcycle or a tractor can already be driven from 14 years upwards.<br>In order to be able to drive on freeways, a vignette must be purchased every year. This can be obtained at customs or at gas stations. The price is currently CHF 40.<br>On highways, the maximum speed is 120km/h, unless otherwise indicated by a sign. A maximum speed of 50km/h applies in built-up areas.</p>
</article>

</body>
</html>
```